Business Card Design for BrightvaleMedia.com

--I need a business card design for my company BrightvaleMedia.com

I have attached my logo...I want the brightvale media logo on the front of the business card, and then I want The Quillstone Chief on the back of it with my information.

I would like to see a light colored background as well as a dark colored background

FRONT:
BRIGHTVALE MEDIA LOGO
248 N. Larkmoor
3rd Floor
San Diego CA 92173
www.BrightvaleMedia.com

Advanced Website & App Development
Websites, Apps, Online Voucher Systems

Leading Edge Marketing Services
SMS, VB, SMM, SEM,

BACK:
QUILLSTONE CHIEF LOGO
Dorian Pelletta
The Quillstone Chief
Call Or Text: 619-555-0148
Dorian@QuillstoneChief.example
www.QuillstoneChief.example

Target Market(s)

small business owners

Industry/Entity Type

Business Consultant

Contact Information for Business Card

FRONT:
BRIGHTVALE MEDIA LOGO
248 N. Larkmoor
3rd Floor
San Diego CA 92173
www.BrightvaleMedia.com

SMS, VB, SMM, SEM,

BACK:
QUILLSTONE CHIEF LOGO
Dorian Pelletta
The Quillstone Chief
Dorian@QuillstoneChief.example
www.QuillstoneChief.example

Requirements
Must have
• add this quote on it somewhere, anywhere,preferrably on back
• "The Fastest Way To Success Is To Take Action”
• — Dorian Pelletta, Quillstone Chief
Nice to have
• open
Should not have
• red

```html
<!DOCTYPE html>
<html lang="en">
<head>
<meta charset="utf-8">
<title>Brightvale Media – Business Cards</title>
<link rel="stylesheet" href="https://fonts.googleapis.com/css2?family=Open+Sans:wght@400;600;700&display=swap">
<style>
  :root {
    --stage: #ececec;
    --card-white: #ffffff;
    --brand-blue: #0b6fae;
    --name-blue: #1a6aa8;
    --band-grey: #6d6e71;
    --text-grey: #58595b;
    --text-light: #ffffff;
    --text-soft: rgba(255,255,255,0.88);
  }
  * { margin: 0; padding: 0; box-sizing: border-box; }
  html, body {
    width: 1200px; height: 900px; overflow: hidden;
    background: var(--stage);
    font-family: "Open Sans", Arial, sans-serif;
  }
  .stage { position: relative; width: 1200px; height: 900px; }

  .card {
    position: absolute;
    overflow: hidden;
    box-shadow: 0 4px 14px rgba(0,0,0,0.15);
  }

  /* Personal side */
  .card--personal {
    left: 238px; top: 60px; width: 555px; height: 345px;
    background: var(--card-white);
  }
  .card__waves { position: absolute; inset: 0; }
  .personal__logo {
    position: absolute; left: 0; right: 0; top: 50px;
    text-align: center;
    font-size: 34px; font-weight: 600; letter-spacing: 3px;
    color: var(--brand-blue);
  }
  .personal__name {
    position: absolute; left: 29px; top: 136px;
    font-size: 18px; font-weight: 700; color: var(--name-blue);
  }
  .personal__title {
    position: absolute; left: 29px; top: 163px;
    font-size: 15px; color: var(--text-grey);
  }
  .contact-list {
    position: absolute; right: 38px; top: 228px;
    list-style: none; text-align: right;
  }
  .contact-list li {
    display: flex; justify-content: flex-end; align-items: center;
    gap: 9px; height: 20.5px;
    font-size: 14px; color: var(--text-light);
  }
  .contact-list svg { width: 11px; height: 11px; fill: var(--text-light); }

  .personal__quote {
    position: absolute; left: 29px; right: 38px; top: 302px;
    text-align: right;
    font-size: 11.5px; line-height: 16px;
    color: var(--text-soft);
  }
  .personal__quote cite { font-style: normal; }

  /* Company side */
  .card--company {
    left: 457px; top: 518px; width: 560px; height: 342px;
    background: var(--brand-blue);
    color: var(--text-light);
    text-align: center;
  }
  .company__logo {
    position: absolute; left: 0; right: 0; top: 50px;
    font-size: 40px; font-weight: 600; letter-spacing: 3px;
  }
  .company__details {
    position: absolute; left: 0; right: 0; top: 156px;
    font-size: 15px; line-height: 20px;
  }
  .company__details p { margin-bottom: 12px; }
  .company__details p.tight { margin-bottom: 14px; }
</style>
</head>
<body>
<main class="stage">

  <section class="card card--personal" aria-label="Personal side of business card">
    <svg class="card__waves" viewBox="0 0 555 345" preserveAspectRatio="none" aria-hidden="true">
      <path d="M0,232 C180,200 380,176 555,168 L555,176 C380,184 200,228 0,270 Z" fill="var(--band-grey)"/>
      <path d="M0,270 C200,226 380,182 555,172 L555,345 L0,345 Z" fill="var(--brand-blue)"/>
    </svg>
    <div class="personal__logo">QUILLSTONE CHIEF</div>
    <h1 class="personal__name">Dorian Pelletta</h1>
    <p class="personal__title">The Quillstone Chief</p>
    <ul class="contact-list">
      <li>619-555-0148
        <svg viewBox="0 0 24 24"><path d="M6.6 10.8a15 15 0 0 0 6.6 6.6l2.2-2.2a1 1 0 0 1 1-.25 11.4 11.4 0 0 0 3.6.57 1 1 0 0 1 1 1V20a1 1 0 0 1-1 1A17 17 0 0 1 3 4a1 1 0 0 1 1-1h3.5a1 1 0 0 1 1 1c0 1.25.2 2.45.57 3.57a1 1 0 0 1-.25 1z"/></svg>
      </li>
      <li>Dorian@QuillstoneChief.example
        <svg viewBox="0 0 24 24"><path d="M2 5h20v14H2z M3.5 6.5 12 13l8.5-6.5" fill="none" stroke="#fff" stroke-width="2.5"/></svg>
      </li>
      <li>www.QuillstoneChief.example
        <svg viewBox="0 0 24 24"><circle cx="12" cy="12" r="10"/><path d="M2 12h20M12 2c3 3 3 17 0 20M12 2c-3 3-3 17 0 20" fill="none" stroke="#0b6fae" stroke-width="1.6"/></svg>
      </li>
    </ul>
    <blockquote class="personal__quote">
      “The Fastest Way To Success Is To Take Action”<br>
      <cite>— Dorian Pelletta, Quillstone Chief</cite>
    </blockquote>
  </section>

  <section class="card card--company" aria-label="Company side of business card">
    <div class="company__logo">BRIGHTVALE MEDIA</div>
    <div class="company__details">
      <p>248 N. Larkmoor 3rd Floor, San Diego CA 92173</p>
      <p>www.BrightvaleMedia.com</p>
      <p class="tight">Advanced Website &amp; App Development | Websites | Apps<br>Online Voucher Systems</p>
      <p>Leading Edge Marketing Services | SMS | VB | SMM | SEM,</p>
    </div>
  </section>

</main>
</body>
</html>
```